Electrician Letterhead Design MVR

We need some letterhead for our bills and other papers.
Customer address is on the right side (Swiss format)
A4 format

Design should also be applicable on Cards

Target Market(s)

Private Customers, Small Business

Industry/Entity Type

Electrician

Other font styles liked:
• incised 901

Colors
00AB8E
00BBA5
67D7C9
C6EFE9
E9F9F6

```html
<!DOCTYPE html>
<html lang="en">
<head>
<meta charset="utf-8">
<title>MVR Letterhead</title>
<link href="https://fonts.googleapis.com/css2?family=Roboto+Slab:wght@400;700&display=swap" rel="stylesheet">
<style>
  :root {
    --backdrop: #dbdbdb;
    --paper: #ffffff;
    --brand: #0f9e8a;
    --brand-light: #67d7c9;
    --ink: #1a1a1a;
    --rule: #cfcfcf;
    --ghost: #e9e9e9;
  }
  * { margin: 0; padding: 0; box-sizing: border-box; }
  html, body { width: 1200px; height: 947px; overflow: hidden; background: var(--backdrop); }
  body { position: relative; font-family: "Roboto Slab", Georgia, serif; color: var(--ink); }

  .letterhead {
    position: absolute; left: 364px; top: 179px;
    width: 472px; height: 605px;
    background: var(--paper);
  }
  .side-band { position: absolute; left: 0; top: 0; width: 8px; height: 100%; background: var(--brand); }

  .brand-name {
    position: absolute; left: 40px; top: 18px;
    font-size: 38px; font-weight: 700; line-height: 1;
    letter-spacing: 1px; color: var(--brand);
  }

  .contact-list {
    position: absolute; left: 300px; top: 22px; height: 34px;
    border-left: 1px solid var(--rule);
    padding-left: 8px; list-style: none;
    display: flex; flex-direction: column; justify-content: space-between;
  }
  .contact-item { display: flex; align-items: center; gap: 5px; font-size: 9px; line-height: 1; white-space: nowrap; }
  .contact-icon { width: 9px; height: 9px; flex: none; }

  .ghost-name {
    position: absolute; left: 0; right: 0; top: 258px;
    text-align: center; font-size: 90px; font-weight: 700; line-height: 1;
    letter-spacing: 4px; color: var(--ghost);
  }

  .address-line {
    position: absolute; left: 40px; width: 390px; top: 580px;
    display: flex; align-items: center; gap: 6px;
    font-size: 10px; white-space: nowrap;
  }
  .address-line::before, .address-line::after {
    content: ""; flex: 1; height: 1px; background: var(--brand-light); opacity: 0.6;
  }
</style>
</head>
<body>
  <main class="letterhead">
    <div class="side-band"></div>

    <div class="brand-name">MVR</div>

    <ul class="contact-list">
      <li class="contact-item">
        <svg class="contact-icon" viewBox="0 0 10 10" aria-hidden="true">
          <rect x="0.6" y="0.6" width="8.8" height="8.8" rx="1.2" fill="none" stroke="var(--brand)" stroke-width="1.2"/>
          <path d="M3 2.4 L4.2 3.8 L3.6 4.5 Q4.6 6.1 5.6 6.5 L6.2 5.8 L7.6 7 L6.8 7.8 Q3.6 7.4 2.3 3.2 Z" fill="var(--brand)"/>
        </svg>
        031-555 010 220
      </li>
      <li class="contact-item">
        <svg class="contact-icon" viewBox="0 0 10 10" aria-hidden="true">
          <rect x="0" y="2" width="10" height="6.5" fill="var(--brand)"/>
          <path d="M0.5 2.5 L5 6 L9.5 2.5 M0.5 8 L3.8 5 M9.5 8 L6.2 5" fill="none" stroke="#fff" stroke-width="0.8"/>
        </svg>
        hello@mvr-strom.ch
      </li>
      <li class="contact-item">
        <svg class="contact-icon" viewBox="0 0 10 10" aria-hidden="true">
          <g fill="none" stroke="var(--brand)" stroke-width="0.9">
            <circle cx="5" cy="5" r="4.3"/>
            <ellipse cx="5" cy="5" rx="1.9" ry="4.3"/>
            <path d="M0.7 5 H9.3 M1.5 2.8 H8.5 M1.5 7.2 H8.5"/>
          </g>
        </svg>
        www.mvr-strom.ch
      </li>
    </ul>

    <div class="ghost-name" aria-hidden="true">MVR</div>

    <p class="address-line">Werkstrasse 12, 8005 Musterstadt, Schweiz</p>
  </main>
</body>
</html>
```